Oral Surgeon Referral Pads

Hello. We need referral pads for Dr Elsabet Quorvane, DDS board certified oral surgeon's new office - Harrowgate Dunmere Oral & Maxillofacial Surgery. See logo uploaded. See some images we would like included
Updates

Designs look the same

Font styles to use
Serif
Script

Colors
00AB8E
00BBA5
67D7C9
C6EFE9
E9F9F6

Requirements
Must have
• Color Pantone 623c. Also foldable business cards

```html
<!DOCTYPE html>
<html lang="en">
<head>
<meta charset="utf-8">
<title>Foldable Card – Harrowgate Dunmere Oral &amp; Maxillofacial Surgery</title>
<link rel="stylesheet" href="https://fonts.googleapis.com/css2?family=Cormorant+Garamond:wght@500&family=EB+Garamond:wght@400&display=swap">
<style>
  :root{
    --backdrop:#b3b3b3;
    --sage:#97b8ac;
    --sage-deep:#8fb2a5;
    --ink:#2f5548;
    --paper:#ffffff;
    --map-base:#e9ece6;
    --map-water:#9fdde6;
  }
  *{margin:0;padding:0;box-sizing:border-box}
  html,body{width:1200px;height:887px;overflow:hidden;background:var(--backdrop)}
  body{position:relative;font-family:"EB Garamond",Georgia,serif;color:var(--ink)}

  .card{position:absolute;top:146px;width:501px;height:570px;overflow:hidden}
  .card--outside{left:74px;background:var(--sage)}
  .card--inside{left:628px;background:var(--paper)}

  /* outside: upper flap is read upside down when folded */
  .flap{position:absolute;left:0;top:0;width:100%;height:286px;transform:rotate(180deg);color:var(--paper);text-align:center}
  .flap > *{position:absolute;left:0;width:100%}
  .practice-name{font-family:"Cormorant Garamond",Georgia,serif;font-weight:500;line-height:1}
  .practice-name--main{top:122px;font-size:30px}
  .practice-name--sub{top:157px;font-size:18px}
  .divider{top:190px;height:1px}
  .divider span{display:block;margin:0 auto;width:26px;height:1px;background:var(--paper)}
  .doctor{top:211px;font-size:19px;letter-spacing:.5px;text-transform:uppercase;line-height:1}
  .doctor-title{top:238px;font-size:14px;line-height:1}

  .lower-panel{position:absolute;left:0;top:286px;width:100%;height:284px;background:var(--sage-deep)}
  .map{position:absolute;left:29px;top:314px;width:434px;height:175px;border-radius:9px;
       background:linear-gradient(135deg,var(--map-base) 0%,#f1efe6 45%,var(--map-water) 120%)}
  .address{position:absolute;left:0;top:493px;width:100%;text-align:center;color:var(--paper);font-size:14.5px;letter-spacing:.2px;text-transform:uppercase}

  .wave{position:absolute;left:0;bottom:0;width:100%;height:60px;display:block}

  /* inside */
  .fold-shade{position:absolute;left:0;top:286px;width:100%;height:34px;background:linear-gradient(#ececec,rgba(255,255,255,0))}
  .credentials{position:absolute;left:40px;top:33px;list-style:none;font-size:18.5px;line-height:20.4px}
  .credentials li{margin-bottom:9px}
  .contact{position:absolute;left:40px;display:flex;align-items:center;gap:8px;font-size:18.5px;line-height:20px;white-space:nowrap}
  .contact--direct{top:240px}
  .contact--office{top:486px}
  .contact svg{width:14px;height:14px;fill:var(--ink);flex:none}
  .contact .gap{width:4px}
  .services{position:absolute;top:318px;font-size:18.5px;line-height:24.6px;list-style:none}
  .services li::before{content:"•";display:inline-block;width:17px;margin-left:-17px;font-size:14px}
  .services--left{left:57px}
  .services--right{left:302px}
</style>
</head>
<body>

<section class="card card--outside" aria-label="Card outside">
  <div class="flap">
    <div class="practice-name practice-name--main">Harrowgate Dunmere</div>
    <div class="practice-name practice-name--sub">Oral &amp; Maxillofacial Surgery</div>
    <div class="divider"><span></span></div>
    <div class="doctor">Elsabet Quorvane, DDS</div>
    <div class="doctor-title">Board Certified Oral and Maxillofacial Surgeon</div>
  </div>
  <div class="lower-panel"></div>
  <div class="map" role="img" aria-label="Street map showing the office location"></div>
  <p class="address">418 Lindmere Ave. Suite 210, Harrowgate, FL 33981</p>
  <svg class="wave" viewBox="0 0 501 60" preserveAspectRatio="none" aria-hidden="true">
    <path d="M0 38 C120 10 230 22 330 30 C420 37 470 22 501 0 L501 60 L0 60 Z" fill="#ffffff"/>
  </svg>
</section>

<section class="card card--inside" aria-label="Card inside">
  <div class="fold-shade"></div>
  <ul class="credentials">
    <li>Diplomate, American Board of<br>Oral &amp; Maxillofacial Surgery</li>
    <li>Diplomate, National Dental<br>Board of Anesthesiology</li>
    <li>Fellow, American Association of<br>Oral &amp; Maxillofacial Surgery</li>
    <li>Fellow, American Dental<br>Society of Anesthesiology</li>
  </ul>
  <p class="contact contact--direct">
    <svg viewBox="0 0 14 14" aria-hidden="true"><path d="M4 0h6a1.5 1.5 0 0 1 1.5 1.5v11A1.5 1.5 0 0 1 10 14H4a1.5 1.5 0 0 1-1.5-1.5v-11A1.5 1.5 0 0 1 4 0zm0 2v9h6V2zm3 10a.7.7 0 1 0 0 .01z"/></svg>
    <span>(555) 214-3307</span><span class="gap"></span>
    <svg viewBox="0 0 14 14" aria-hidden="true"><path d="M0 3h14v1L7 8 0 4zm0 2.3 7 4 7-4V11H0z"/></svg>
    <span>Dr.Quorvane@hdoms.com</span>
  </p>
  <ul class="services services--left">
    <li>Dental Implants</li><li>Surgical Extractions</li><li>Bone Graft</li>
    <li>All-on-X</li><li>Wisdom Teeth</li><li>Reconstructive Surgery</li>
  </ul>
  <ul class="services services--right">
    <li>IV Sedation</li><li>Oral Infections</li><li>Surgical Pathology</li>
    <li>PRP/PRF</li><li>Facial Trauma</li><li>Sinus Augmentation</li>
  </ul>
  <p class="contact contact--office">
    <svg viewBox="0 0 14 14" aria-hidden="true"><path d="M3 1l2 3-1.3 1.5a8 8 0 0 0 4.8 4.8L10 9l3 2-1 2.5C6 13 1 8 .5 2z"/></svg>
    <span>(555) 214-3380</span><span class="gap"></span>
    <svg viewBox="0 0 14 14" aria-hidden="true"><path d="M3 0h8v4H3zM1 5h12v6h-2v3H3v-3H1zm3 4v4h6V9z"/></svg>
    <span>(555) 214-3381</span><span class="gap"></span>
    <svg viewBox="0 0 14 14" aria-hidden="true"><path d="M7 0a7 7 0 1 1 0 14A7 7 0 0 1 7 0zm0 1.5a5.5 5.5 0 1 0 0 11 5.5 5.5 0 0 0 0-11zM1.5 7h11v1h-11zM6.5 1.5h1v11h-1z"/></svg>
    <span>hdoms.com</span>
  </p>
  <svg class="wave" viewBox="0 0 501 60" preserveAspectRatio="none" aria-hidden="true">
    <path d="M0 38 C120 10 230 22 330 30 C420 37 470 22 501 0 L501 60 L0 60 Z" fill="#97b8ac"/>
  </svg>
</section>

</body>
</html>
```